Tobias Ränkel and Co stationary design

Name of business:
Tobias Ränkel and Co

Can be written as:
Tobias Ränkel and Co
Tobias Ränkel & Co
tobias ränkel & co

If broken into letters:
TR&Co
tr&co

We are a Railway Safety Training Company
Our focus is on rail safety, Rail Management, Safety Management, Train Control Training, Accident Investigation.

.

Project Deadline Extended Reason: The original date was set to commence as soon as the logo contest finished. Sketch harbor started the project as soon as it was paid. Added Thursday, May 12, 2016

Target Market(s)

Professionals, CEO's and Managing Directors

Industry/Entity Type

Management Consulting

Font styles to use
Sans Serif

Requirements
Must have
• Professional, Sharp, Creative and modern
• Please note that this is for stationary concept which must include
• - business card
• - letterhead
• - envelope
• - with compliments slip
• - document cover (like book or folder cover)
• - dividers for folders....
• These must all have a common theme or style
Nice to have
• Keep if fresh
Should not have
• Please don't sent just fonts.... Must be creative

```html
<!DOCTYPE html>
<html lang="en">
<head>
<meta charset="utf-8">
<title>Tobias Ränkel &amp; Co — Stationery</title>
<link rel="stylesheet" href="https://fonts.googleapis.com/css2?family=Open+Sans:wght@400;600;700&display=swap">
<style>
  :root {
    --navy: #14498f;
    --navy-soft: #2a5c9e;
    --orange: #f7a52b;
    --paper: #ffffff;
    --backdrop: #a9a9a9;
    --ink: #222222;
    --shadow: 4px 8px 12px rgba(0,0,0,.45);
  }
  * { box-sizing: border-box; margin: 0; padding: 0; }
  html, body { width: 1200px; height: 1200px; overflow: hidden; }
  body { background: var(--backdrop); font-family: "Open Sans", Arial, sans-serif; position: relative; }
  .sheet { position: absolute; background: var(--paper); box-shadow: var(--shadow); overflow: hidden; }
  .swoosh { position: absolute; left: 0; top: 0; width: 100%; display: block; }
  .brand { position: absolute; display: flex; align-items: center; gap: 6px; color: var(--navy); font-weight: 600; white-space: nowrap; }
  .brand .dot { border-radius: 50%; background: var(--navy); flex: none; }
  .brand.light { color: #fff; }
  .brand.light .dot { background: var(--orange); }

  .person { position: absolute; left: 26px; font-size: 8px; color: var(--ink); line-height: 1.25; }
  .person strong { display: block; color: var(--navy); font-weight: 600; font-size: 9.5px; }
  .contacts { position: absolute; left: 134px; width: 126px; border-left: 1px solid var(--navy); padding-left: 9px; font-size: 7.4px; color: var(--ink); line-height: 1.5; white-space: nowrap; }
  .contacts li { list-style: none; display: flex; align-items: center; gap: 4px; }
  .contacts svg { width: 7px; height: 7px; fill: var(--navy); flex: none; }
  .contacts .address { color: var(--navy); margin-top: 3px; display: block; line-height: 1.25; }

  .compliments-title { position: absolute; right: 14px; top: 28px; color: var(--navy); font-size: 11.5px; }
  .pattern-field { position: absolute; inset: 0; background: var(--navy); }
  .small-address { position: absolute; border-left: 1px solid var(--navy); padding-left: 5px; font-size: 4.5px; color: var(--navy); line-height: 1.3; white-space: nowrap; }

  .letter-footer { position: absolute; left: 0; right: 0; bottom: 18px; text-align: center; font-size: 6.5px; color: var(--ink); }
  .letter-footer .row { display: flex; justify-content: center; gap: 14px; }
  .letter-footer .address { color: var(--navy); font-size: 7px; margin-top: 4px; }
  .letter-base { position: absolute; left: 0; right: 0; bottom: 0; height: 8px; background: var(--navy); }

  .folder { background: var(--navy); }
  .folder-footer { position: absolute; left: 14px; bottom: 28px; display: flex; gap: 8px; align-items: center; color: #d6e1f0; font-size: 4px; line-height: 1.4; white-space: nowrap; }
  .folder-footer span { border-left: 1px solid #d6e1f0; padding-left: 4px; }
</style>
</head>
<body>

<!-- Business card front -->
<section class="sheet card" style="left:52px;top:41px;width:268px;height:162px">
  <svg class="swoosh" viewBox="0 0 268 50" preserveAspectRatio="none"><path d="M0 0H268V22Q150 4 0 20Z" fill="var(--navy)"/><path d="M0 22Q80 10 150 12Q70 18 0 48Z" fill="var(--orange)"/></svg>
  <p class="person" style="top:50px"><strong>Marcus Lindqvist</strong>Director</p>
  <div class="brand" style="left:22px;top:130px;font-size:8px"><span class="dot" style="width:9px;height:9px"></span>Tobias Ränkel &amp; Co</div>
  <ul class="contacts" style="top:73px">
    <li><svg viewBox="0 0 8 8"><rect x="2" y="0" width="4" height="8" rx="1"/></svg>+61 355 208 4417</li>
    <li><svg viewBox="0 0 8 8"><path d="M2 0L4 2 3 3Q4 5 5 5L6 4 8 6 6 8Q0 7 0 2Z"/></svg>+61 388 640 2195</li>
    <li><svg viewBox="0 0 8 8"><path d="M0 2H8V7H0ZM0 2L4 5 8 2"/></svg>info@trcotraining.com.au</li>
    <li><svg viewBox="0 0 8 8"><circle cx="4" cy="4" r="4"/></svg>www.trcotraining.com.au</li>
    <li class="address">58 Harbour Lane, Suite 210<br>Parramatta, NSW 2150</li>
  </ul>
</section>

<!-- Business card back -->
<section class="sheet card" style="left:345px;top:41px;width:268px;height:162px">
  <svg class="swoosh" viewBox="0 0 268 50" preserveAspectRatio="none"><path d="M0 0H268V22Q150 4 0 20Z" fill="var(--navy)"/><path d="M0 22Q80 10 150 12Q70 18 0 48Z" fill="var(--orange)"/></svg>
  <div class="brand" style="left:68px;top:118px;font-size:12.5px"><span class="dot" style="width:12px;height:12px"></span>Tobias Ränkel &amp; Co</div>
</section>

<!-- Compliments slip -->
<section class="sheet slip" style="left:677px;top:34px;width:338px;height:169px">
  <svg class="swoosh" viewBox="0 0 338 50" preserveAspectRatio="none"><path d="M0 0H338V18Q190 6 0 18Z" fill="var(--navy)"/><path d="M0 20Q110 10 190 12Q90 16 0 44Z" fill="var(--orange)"/></svg>
  <p class="compliments-title">With Compliments</p>
  <div class="brand" style="left:20px;top:148px;font-size:5px;gap:3px"><span class="dot" style="width:5px;height:5px"></span>Tobias Ränkel &amp; Co</div>
</section>

<!-- Business card variant -->
<section class="sheet card" style="left:52px;top:239px;width:268px;height:162px">
  <p class="person" style="top:18px;left:16px"><strong>Marcus Lindqvist</strong>Director</p>
  <div class="brand" style="left:18px;top:131px;font-size:9px"><span class="dot" style="width:10px;height:10px"></span>Tobias Ränkel &amp; Co</div>
  <ul class="contacts" style="top:74px">
    <li><svg viewBox="0 0 8 8"><rect x="2" y="0" width="4" height="8" rx="1"/></svg>+61 355 208 4417</li>
    <li><svg viewBox="0 0 8 8"><path d="M2 0L4 2 3 3Q4 5 5 5L6 4 8 6 6 8Q0 7 0 2Z"/></svg>+61 388 640 2195</li>
    <li><svg viewBox="0 0 8 8"><path d="M0 2H8V7H0ZM0 2L4 5 8 2"/></svg>info@trcotraining.com.au</li>
    <li><svg viewBox="0 0 8 8"><circle cx="4" cy="4" r="4"/></svg>www.trcotraining.com.au</li>
    <li class="address">58 Harbour Lane, Suite 210<br>Parramatta, NSW 2150</li>
  </ul>
</section>

<!-- Business card patterned back -->
<section class="sheet card" style="left:345px;top:239px;width:268px;height:162px">
  <div class="pattern-field" role="img" aria-label="Repeating brand pattern in tonal navy"></div>
  <div class="brand light" style="left:180px;top:113px;font-size:6px;gap:3px"><span class="dot" style="width:6px;height:6px"></span>Tobias Ränkel &amp; Co</div>
</section>

<!-- Envelope front -->
<section class="sheet envelope" style="left:677px;top:226px;width:397px;height:199px">
  <svg class="swoosh" viewBox="0 0 397 50" preserveAspectRatio="none"><path d="M0 0H397V20Q220 8 0 22Z" fill="var(--navy)"/><path d="M0 24Q130 12 220 14Q110 18 0 48Z" fill="var(--orange)"/></svg>
  <div class="brand" style="left:16px;top:182px;font-size:4.5px;gap:3px"><span class="dot" style="width:5px;height:5px"></span>Tobias Ränkel &amp; Co</div>
  <p class="small-address" style="left:72px;top:175px">58 Harbour Lane, Suite 210<br>Parramatta, NSW 2150</p>
</section>

<!-- Envelope back -->
<section class="sheet envelope" style="left:677px;top:443px;width:393px;height:196px">
  <svg class="swoosh" viewBox="0 0 393 60"><path d="M0 0H393L380 42Q376 59 362 59H32Q18 59 12 42Z" fill="var(--navy)"/></svg>
  <div class="brand light" style="left:160px;top:24px;font-size:6px;gap:3px"><span class="dot" style="width:6px;height:6px"></span>Tobias Ränkel &amp; Co</div>
</section>

<!-- Letterhead -->
<section class="sheet letterhead" style="left:54px;top:485px;width:455px;height:646px">
  <svg class="swoosh" viewBox="0 0 455 80" preserveAspectRatio="none"><path d="M0 0H455V32Q270 14 0 36Z" fill="var(--navy)"/><path d="M0 38Q150 18 260 22Q120 30 0 74Z" fill="var(--orange)"/></svg>
  <div class="brand" style="left:308px;top:100px;font-size:10.5px"><span class="dot" style="width:11px;height:11px"></span>Tobias Ränkel &amp; Co</div>
  <div class="letter-footer">
    <div class="row"><span>+61 388 640 2195</span><span>info@trcotraining.com.au</span><span>www.trcotraining.com.au</span></div>
    <div class="address">58 Harbour Lane, Suite 210, Parramatta, NSW 2150</div>
  </div>
  <div class="letter-base"></div>
</section>

<!-- Document folder cover -->
<section class="sheet folder" style="left:613px;top:690px;width:528px;height:440px">
  <svg class="swoosh" viewBox="0 0 528 440"><path d="M320 0H528V200Q400 190 350 90Q330 50 320 0Z" fill="var(--paper)"/><path d="M330 46Q360 150 440 180Q490 196 528 196V206Q470 204 420 185Q355 150 330 46Z" fill="var(--orange)"/></svg>
  <div class="brand" style="left:398px;top:105px;font-size:10.5px"><span class="dot" style="width:11px;height:11px"></span>Tobias Ränkel &amp; Co</div>
  <div class="folder-footer">
    <p>Tobias Ränkel &amp; Co</p>
    <span>+61 355 208 4417<br>+61 388 640 2195</span>
    <span>info@trcotraining.com.au<br>www.trcotraining.com.au</span>
    <span>58 Harbour Lane, Suite 210<br>Parramatta, NSW 2150</span>
  </div>
</section>

</body>
</html>
```